Window cleaning and Pressure washing

Truck wrap partial or full/background:
Would like to see a background of a water mark or something related to window cleaning. And or pressure washing.

Doors of the truck:
Need to have my logo printed in big on the doors and with LLC in small after the logo. Need to have my slogan below my logo on the door.
Slogan is; “Affordable 5 star services!”

Sides of the truck:
Want to see window cleaning and Pressure washing on the sides of the truck in big letters with the phone number. Slanted with a shadow effect.
(Would like to see slanted and not slanted) also need to see something that signifies 100% satisfaction or your money back!Preferably a sticker, Or a combination of both. Also need to have residential and commercial somewhere.
Phone number needs to be on here.

Tailgate:
Want to have the services on the back tailgate with the slogan, as well as the 100% money back guarantee sticker.
And the phone number here to!

Back window;
Needs to have the same background as the wrap on the truck or very slimier with the water swiped away Clean with the logo presented as shown in one of the pictures below.

```html
<!DOCTYPE html>
<html lang="en">
<head>
<meta charset="utf-8">
<title>Clear Peak LLC – Truck Wrap</title>
<link href="https://fonts.googleapis.com/css2?family=Montserrat:wght@600;700;800&family=Oswald:wght@500;700&display=swap" rel="stylesheet">
<style>
  :root {
    --wrap-blue: #3aa8dc;
    --wrap-blue-deep: #1c80c6;
    --wrap-blue-light: #5cc0ec;
    --accent-orange: #f7a600;
    --bright-blue: #1aa7f0;
    --ink: #222;
    --white: #fff;
  }
  html, body { margin: 0; padding: 0; }
  body {
    width: 1098px; height: 1200px; overflow: hidden;
    background: var(--white);
  }
  .wrap-sheet { display: block; width: 1098px; height: 1200px; }
  .label-sans { font-family: 'Montserrat', sans-serif; }
  .label-condensed { font-family: 'Oswald', sans-serif; font-weight: 700; }
  .brand-name { font-family: 'Montserrat', sans-serif; font-weight: 800; fill: var(--white); }
</style>
</head>
<body>
<svg class="wrap-sheet" viewBox="0 0 1098 1200" xmlns="http://www.w3.org/2000/svg">
  <defs>
    <linearGradient id="waterBg" x1="0" y1="0" x2="1" y2="1">
      <stop offset="0" stop-color="var(--wrap-blue-light)"/>
      <stop offset="0.5" stop-color="var(--wrap-blue)"/>
      <stop offset="1" stop-color="#2b98d2"/>
    </linearGradient>
    <linearGradient id="silverText" x1="0" y1="0" x2="0" y2="1">
      <stop offset="0" stop-color="#ffffff"/>
      <stop offset="0.55" stop-color="#e4e4e4"/>
      <stop offset="1" stop-color="#8e8e8e"/>
    </linearGradient>
    <linearGradient id="silverBand" x1="0" y1="0" x2="1" y2="0">
      <stop offset="0" stop-color="#9a9a9a"/>
      <stop offset="0.5" stop-color="#f4f4f4"/>
      <stop offset="1" stop-color="#a8a8a8"/>
    </linearGradient>
    <linearGradient id="cleanWindowPhoto" x1="0" y1="0" x2="1" y2="1">
      <stop offset="0" stop-color="#8fa3b6"/>
      <stop offset="0.5" stop-color="#c9d3cf"/>
      <stop offset="1" stop-color="#9fb58a"/>
    </linearGradient>
    <linearGradient id="yellowFade" x1="0" y1="0" x2="1" y2="0">
      <stop offset="0" stop-color="var(--wrap-blue)"/>
      <stop offset="0.35" stop-color="var(--accent-orange)"/>
    </linearGradient>
    <filter id="textShadow" x="-10%" y="-10%" width="120%" height="140%">
      <feDropShadow dx="1.5" dy="2" stdDeviation="0.8" flood-color="#000" flood-opacity="0.7"/>
    </filter>
    <symbol id="iconPhone" viewBox="0 0 24 24">
      <path d="M6.6 2.5l3 3.2-1.8 2.4c1.2 2.8 3.2 4.9 6 6.1l2.4-1.8 3.3 3-1.6 3.6C10.6 18.8 5.2 13.4 3 5.1z" fill="currentColor"/>
    </symbol>
    <symbol id="iconTick" viewBox="0 0 24 24">
      <circle cx="12" cy="12" r="10" fill="var(--white)" stroke="var(--accent-orange)" stroke-width="2.6"/>
      <path d="M7.5 12.3l3 3 6-6.3" fill="none" stroke="var(--accent-orange)" stroke-width="2.4" stroke-linecap="round" stroke-linejoin="round"/>
    </symbol>
  </defs>

  <!-- ===== Side panel ===== -->
  <g class="side-panel">
    <path fill="url(#waterBg)" fill-rule="evenodd" role="img" aria-label="Blue water droplet texture"
      d="M51,249 L54,240 Q160,210 276,201 L324,198 Q380,150 432,114 L582,99 Q598,100 600,108 L612,204 L1050,201 L1053,228 L1020,240 L1020,309 L1050,309 L1050,324 L1014,324 L1011,387 L939,390 L939,336 Q900,276 840,276 Q770,280 744,336 L744,384 L309,391 L306,330 Q280,276 204,276 Q140,280 120,300 L120,306 L105,306 L105,252 Z
         M368,198 Q405,150 470,116 L548,112 Q558,112 558,122 L560,212 L370,216 Q354,214 368,198 Z"/>
    <polygon class="side-deep-panel" points="500,216 712,204 740,384 560,388 540,300" fill="var(--wrap-blue-deep)" opacity="0.55"/>
    <rect class="door-handle" x="504" y="245" width="57" height="9" rx="4" fill="var(--white)"/>

    <text class="label-sans" x="143" y="241" font-size="16.5" font-weight="600" fill="var(--white)">LICENSED AND</text>
    <rect x="143" y="245" width="131" height="20" fill="var(--accent-orange)"/>
    <text class="label-sans" x="208" y="261" font-size="15" font-weight="700" fill="var(--white)" text-anchor="middle" letter-spacing="5">INSURED</text>

    <text class="brand-name" x="420" y="278" font-size="34" text-anchor="middle">CLEAR</text>
    <text class="brand-name" x="410" y="316" font-size="34" text-anchor="middle">PEAK</text>
    <text class="label-sans" x="460" y="316" font-size="14" font-weight="700" fill="var(--white)">LLC</text>

    <polygon points="294,324 515,324 528,351 306,351" fill="url(#yellowFade)"/>
    <text class="label-sans" x="422" y="347" font-size="22" font-weight="800" fill="var(--white)" text-anchor="middle">AFFORDABLE</text>
    <polygon points="330,354 675,354 680,381 342,381" fill="var(--bright-blue)"/>
    <text class="label-sans" x="474" y="377" font-size="23" font-weight="800" fill="var(--white)" text-anchor="middle">5 STAR SERVICES!</text>

    <g class="label-condensed" font-size="31" fill="url(#silverText)" filter="url(#textShadow)" stroke="#333" stroke-width="0.6">
      <text x="574" y="247">WINDOW</text>
      <text x="574" y="280">CLEANING AND</text>
      <text x="574" y="313">PRESSURE</text>
      <text x="574" y="346">WASHING</text>
    </g>

    <polygon points="725,204 1050,201 1053,228 1036,246 750,246" fill="var(--accent-orange)"/>
    <circle cx="738" cy="228" r="17" fill="var(--bright-blue)" stroke="var(--white)" stroke-width="3"/>
    <use href="#iconPhone" x="729" y="219" width="18" height="18" color="var(--white)"/>
    <text class="label-condensed" x="768" y="243" font-size="36" fill="url(#silverText)" stroke="#333" stroke-width="0.8" filter="url(#textShadow)">(555) 014-2290</text>
    <rect x="791" y="251" width="200" height="19" fill="var(--white)"/>
    <text class="label-sans" x="891" y="265" font-size="13" font-weight="700" fill="var(--bright-blue)" text-anchor="middle">Commercial &amp; Residential</text>

    <g class="guarantee-sticker-small">
      <text class="label-condensed" x="978" y="307" font-size="28" fill="var(--accent-orange)" stroke="#7a5200" stroke-width="0.6" text-anchor="middle">100%</text>
      <rect x="945" y="310" width="66" height="21" rx="3" fill="var(--ink)"/>
      <text x="978" y="320" font-family="Oswald, sans-serif" font-size="7.5" fill="var(--white)" text-anchor="middle">SATISFACTION OR</text>
      <rect x="948" y="322" width="60" height="7" fill="var(--white)"/>
      <text x="978" y="328" font-family="Oswald, sans-serif" font-weight="700" font-size="6" fill="var(--bright-blue)" text-anchor="middle">YOUR MONEY BACK!</text>
      <text x="978" y="344" font-size="9" fill="#ffe000" text-anchor="middle" letter-spacing="1">★★★★★</text>
      <text class="label-sans" x="978" y="360" font-size="7" font-weight="600" fill="var(--white)" text-anchor="middle">Follow Us</text>
      <circle cx="969" cy="372" r="6" fill="var(--white)"/>
      <circle cx="987" cy="372" r="6" fill="var(--white)"/>
    </g>
  </g>

  <!-- ===== Tailgate ===== -->
  <g class="tailgate">
    <path fill="url(#waterBg)" fill-rule="evenodd" role="img" aria-label="Blue water droplet texture"
      d="M174,762 L175,474 L191,474 L195,507 L914,507 L917,476 L933,476 L933,762 Z
         M490,519 L618,519 Q624,519 622,526 L615,572 Q613,579 606,579 L502,579 Q495,579 493,572 L486,526 Q484,519 490,519 Z"/>
    <g class="label-condensed" font-size="30" fill="url(#silverText)" stroke="#333" stroke-width="0.6" filter="url(#textShadow)">
      <text x="243" y="556">WINDOW CLEANING</text>
      <text x="243" y="599">HOUSE WASHING</text>
      <text x="243" y="642">PRESSURE WASHING</text>
      <text x="688" y="556">ROOF CLEANING</text>
      <text x="688" y="599">GUTTER CLEANING</text>
      <text x="688" y="642">SCREEN REPAIRS</text>
    </g>
    <use href="#iconTick" x="207" y="532" width="24" height="24"/>
    <use href="#iconTick" x="207" y="575" width="24" height="24"/>
    <use href="#iconTick" x="207" y="618" width="24" height="24"/>
    <use href="#iconTick" x="653" y="532" width="24" height="24"/>
    <use href="#iconTick" x="653" y="575" width="24" height="24"/>
    <use href="#iconTick" x="653" y="618" width="24" height="24"/>
    <text class="label-condensed" x="554" y="628" font-size="16" fill="var(--white)" text-anchor="middle" letter-spacing="1">ARVEN</text>

    <rect x="172" y="672" width="761" height="90" fill="var(--bright-blue)"/>
    <polygon points="210,672 750,672 795,762 267,762" fill="var(--accent-orange)"/>
    <polygon points="750,672 933,672 933,762 795,762" fill="var(--white)"/>
    <circle cx="233" cy="715" r="29" fill="var(--accent-orange)" stroke="var(--white)" stroke-width="4"/>
    <use href="#iconPhone" x="217" y="699" width="32" height="32" color="var(--white)"/>
    <text class="label-condensed" x="288" y="745" font-size="66" fill="url(#silverText)" stroke="#333" stroke-width="1.2" filter="url(#textShadow)">(555) 014-2290</text>

    <g class="guarantee-sticker">
      <text class="label-condensed" x="848" y="689" font-size="44" fill="var(--accent-orange)" stroke="#7a5200" stroke-width="0.8" text-anchor="middle">100%</text>
      <rect x="795" y="693" width="107" height="33" rx="5" fill="var(--ink)"/>
      <text x="848" y="707" font-family="Oswald, sans-serif" font-weight="500" font-size="11.5" fill="var(--white)" text-anchor="middle">SATISFACTION OR</text>
      <rect x="801" y="711" width="95" height="12" fill="var(--white)"/>
      <text x="848" y="721" font-family="Oswald, sans-serif" font-weight="700" font-size="9.5" fill="var(--ink)" text-anchor="middle">YOUR MONEY BACK!</text>
      <text x="848" y="747" font-size="13" fill="#ffd400" text-anchor="middle" letter-spacing="2">★★★★★</text>
    </g>
  </g>

  <!-- ===== Back window ===== -->
  <g class="back-window">
    <path fill="url(#waterBg)" role="img" aria-label="Blue water droplet texture"
      d="M300,890 Q540,862 800,884 Q820,886 824,900 L852,1080 L252,1080 L288,905 Q290,892 300,890 Z"/>
    <path fill="url(#cleanWindowPhoto)" role="img" aria-label="Photo of a squeegee wiping a soapy window in front of a house"
      d="M684,879 L800,884 Q820,886 824,900 L852,1080 L525,1080 Z"/>
    <polygon points="645,879 684,879 525,1080 483,1080" fill="url(#silverBand)"/>
    <text class="brand-name" x="322" y="978" font-size="52">CLEAR</text>
    <text class="brand-name" x="322" y="1036" font-size="52">PEAK</text>
  </g>
</svg>
</body>
</html>
```